wedding officIate wedding day coordination wedding planning

We offer elopement packages featuring asheville NC as a destination for ceremony
we offer wedding officiate services , premarital coaching
wedding planning for small events
wedding day coordination services

Wedding

Past a lantern
dream elopementa & lovely little weddings
Marisol Benavente
Asheville NC

```html
<!DOCTYPE html>
<html lang="en">
<head>
<meta charset="utf-8">
<title>Past a lantern — business cards</title>
<link href="https://fonts.googleapis.com/css2?family=Great+Vibes&family=Raleway:wght@400;500&display=swap" rel="stylesheet">
<style>
  :root {
    --sun-light: #f6e15e;
    --sun: #f2c230;
    --sun-deep: #ebb224;
    --slate: #6b6b6d;
    --ink: #5a5a5c;
    --white: #ffffff;
    --backdrop: #efece6;
  }
  * { margin: 0; padding: 0; box-sizing: border-box; }
  html, body { width: 1200px; height: 1000px; overflow: hidden; }
  body { background: var(--backdrop); position: relative; font-family: "Raleway", sans-serif; }

  .card {
    position: absolute;
    width: 700px;
    height: 400px;
    overflow: hidden;
    box-shadow: 0 10px 28px rgba(0,0,0,0.18);
  }

  /* Front card */
  .card-front {
    left: 110px; top: 70px;
    background: radial-gradient(ellipse at 60% 35%, var(--sun-light) 0%, var(--sun) 70%, var(--sun-deep) 100%);
  }
  .front-artwork {
    position: absolute; left: 0; top: 90px;
    width: 300px; height: 170px;
    background: linear-gradient(135deg, rgba(89,89,91,0.55), rgba(89,89,91,0.25));
    border-radius: 4px;
  }
  .front-brand {
    position: absolute; right: 40px; top: 175px;
    width: 330px;
    text-align: center; color: var(--ink);
  }
  .brand-name {
    font-family: "Great Vibes", cursive;
    font-size: 62px; line-height: 1.05; font-weight: 400;
    white-space: nowrap;
  }
  .brand-tagline {
    font-size: 14px; letter-spacing: 0.3px; margin-top: 8px;
    white-space: nowrap;
  }

  /* Back card */
  .card-back { left: 390px; top: 500px; background: var(--slate); }
  .back-shape { position: absolute; inset: 0; }
  .back-brand {
    position: absolute; left: 230px; top: 70px;
    width: 330px;
    text-align: center;
  }
  .back-brand .brand-name { color: var(--white); font-size: 58px; }
  .back-brand .brand-tagline { color: var(--sun); font-size: 13px; }

  .holder-name {
    position: absolute; left: 36px; bottom: 30px;
    font-family: "Great Vibes", cursive;
    font-size: 46px; color: var(--ink);
    white-space: nowrap;
  }
  .contact-list {
    position: absolute; right: 30px; bottom: 108px;
    list-style: none; color: var(--ink);
  }
  .contact-item {
    display: flex; align-items: center; gap: 10px;
    font-size: 21px; margin-top: 6px;
    white-space: nowrap;
  }
  .contact-icon { width: 26px; height: 26px; flex: none; }
</style>
</head>
<body>

<section class="card card-front" aria-label="Card front">
  <div class="front-artwork" role="img" aria-label="Illustration of two lovebirds on a branch with small hearts"></div>
  <div class="front-brand">
    <div class="brand-name">Past a lantern</div>
    <div class="brand-tagline">Intimate ceremonies in the Blue Ridge hills</div>
  </div>
</section>

<section class="card card-back" aria-label="Card back">
  <svg class="back-shape" viewBox="0 0 700 400" preserveAspectRatio="none" aria-hidden="true">
    <defs>
      <linearGradient id="band" x1="0" y1="0" x2="1" y2="0">
        <stop offset="0" stop-color="#f2c230"/>
        <stop offset="0.5" stop-color="#f6e15e"/>
        <stop offset="1" stop-color="#f2c230"/>
      </linearGradient>
    </defs>
    <path d="M0 400 L0 330 C220 300 480 230 700 150 L700 400 Z" fill="url(#band)"/>
    <path d="M0 330 C220 300 480 230 700 150 L700 140 C480 222 220 294 0 326 Z" fill="#ffffff"/>
  </svg>

  <div class="back-brand">
    <div class="brand-name">Past a lantern</div>
    <div class="brand-tagline">Intimate ceremonies in the Blue Ridge hills</div>
  </div>

  <ul class="contact-list">
    <li class="contact-item">
      <svg class="contact-icon" viewBox="0 0 26 26" aria-hidden="true">
        <circle cx="13" cy="13" r="12" fill="#5a5a5c"/>
        <rect x="9" y="6" width="8" height="14" rx="1.5" fill="none" stroke="#f2c230" stroke-width="1.6"/>
        <rect x="10.5" y="8" width="5" height="7" fill="#f2c230"/>
      </svg>
      828-555-0147
    </li>
    <li class="contact-item">
      <svg class="contact-icon" viewBox="0 0 26 26" aria-hidden="true">
        <circle cx="13" cy="13" r="12" fill="#5a5a5c"/>
        <rect x="6.5" y="8.5" width="13" height="9" fill="none" stroke="#f2c230" stroke-width="1.6"/>
        <path d="M6.5 8.5 L13 13.5 L19.5 8.5" fill="none" stroke="#f2c230" stroke-width="1.6"/>
      </svg>
      hello@pastalantern.net
    </li>
  </ul>

  <div class="holder-name">Marisol Benavente</div>
</section>

</body>
</html>
```